Velvet Lantern rebranding my business with a new business card

I have my new logo and now I need a refresher on my business cards. I really want something fun and fresh. I like black background or anything to make the color pop.
Logo
Name: Velvet Lantern
Contact Info as stated below:
Mira Pellow
555-013-4762
Logo
Name: Velvet Lantern
Mira Pellow
555-013-4762
fb.me/VelvetLanternbyMira
Instagram: @VelvetLanternbyMira

Industry/Entity Type

Business

Contact Information for Business Card

double-sided. Logo on one side. Contact info on the other.

Requirements
Must have
• Logo
• Name: Velvet Lantern
• Contact Info as stated below:
• Mira Pellow
• 555-013-4762
• fb.me/VelvetLanternbyMira
• fb.me/VelvetLanternbyMira

```html
<!DOCTYPE html>
<html lang="en">
<head>
<meta charset="utf-8">
<title>Velvet Lantern – Business Card</title>
<link rel="stylesheet" href="https://fonts.googleapis.com/css2?family=Roboto:wght@400;500;700&display=swap">
<style>
  :root {
    --backdrop: #e9e6e2;
    --card-dark: #1c1d1f;
    --card-light: #f2f2f2;
    --ink: #2b2b2b;
    --ink-soft: #4a4a4a;
    --white: #ffffff;
    --blush: #f2a9bb;
    --blush-deep: #e98aa3;
    --band: #0d0d0d;
  }
  * { margin: 0; padding: 0; box-sizing: border-box; }
  html, body { width: 1200px; height: 960px; overflow: hidden; }
  body {
    position: relative;
    background: var(--backdrop);
    font-family: "Roboto", Arial, sans-serif;
  }
  .card {
    position: absolute;
    border-radius: 16px;
    overflow: hidden;
  }
  .card-front {
    left: 320px; top: 100px;
    width: 610px; height: 355px;
    background: var(--card-dark);
  }
  .front-logo {
    position: absolute;
    left: 0; right: 0; top: 160px;
    text-align: center;
    color: var(--white);
    font-weight: 500;
    font-size: 30px;
    letter-spacing: 1px;
  }
  .front-logo .dot {
    display: inline-block;
    width: 14px; height: 14px;
    border-radius: 50%;
    background: var(--blush);
    margin-right: 12px;
    vertical-align: 4px;
  }
  .front-web {
    position: absolute;
    left: 0; right: 0; top: 297px;
    text-align: center;
    color: var(--white);
    font-size: 14px;
    letter-spacing: 6px;
  }
  .card-back {
    left: 320px; top: 493px;
    width: 600px; height: 342px;
    background: var(--card-light);
  }
  .badge {
    position: absolute;
    left: 381px; top: 35px;
    width: 174px; height: 174px;
    border-radius: 50%;
    background: var(--white);
    border: 1.5px solid #222;
    display: flex; align-items: center; justify-content: center;
  }
  .badge::before {
    content: "";
    position: absolute; inset: 5px;
    border-radius: 50%;
    border: 2px solid var(--blush);
  }
  .badge-name {
    color: var(--ink);
    font-weight: 500;
    font-size: 19px;
    text-align: center;
    line-height: 1.2;
  }
  .contact-name {
    position: absolute;
    left: 32px; top: 195px;
    font-weight: 700;
    font-size: 21px;
    color: var(--ink);
  }
  .contact-list {
    position: absolute;
    left: 33px; top: 236px;
    list-style: none;
    font-size: 14px;
    color: var(--ink-soft);
    line-height: 20px;
  }
  .contact-list li { display: flex; align-items: center; gap: 8px; }
  .contact-list svg, .contact-list .square { width: 13px; height: 13px; flex: none; }
  .contact-list .square { background: #333; border-radius: 1px; }
  .back-footer { position: absolute; left: 0; bottom: 0; width: 600px; height: 42px; }
  .back-web {
    position: absolute;
    right: 20px; bottom: 12px;
    color: var(--white);
    font-size: 14px;
  }
</style>
</head>
<body>
  <section class="card card-front">
    <div class="front-logo"><span class="dot"></span>Velvet Lantern</div>
    <div class="front-web">www.velvetlantern-cakes.com</div>
  </section>

  <section class="card card-back">
    <div class="badge"><div class="badge-name">Velvet<br>Lantern</div></div>
    <div class="contact-name">MIRA PELLOW</div>
    <ul class="contact-list">
      <li>
        <svg viewBox="0 0 24 24" aria-hidden="true"><path fill="#333" d="M6.6 10.8a15.1 15.1 0 0 0 6.6 6.6l2.2-2.2c.3-.3.7-.4 1-.2 1.1.4 2.3.6 3.6.6.6 0 1 .4 1 1V20c0 .6-.4 1-1 1C10.6 21 3 13.4 3 4c0-.6.4-1 1-1h3.5c.6 0 1 .4 1 1 0 1.3.2 2.5.6 3.6.1.3 0 .7-.2 1z"/></svg>
        555-013-4762
      </li>
      <li><span class="square"></span>fb.me/VelvetLanternbyMira</li>
    </ul>
    <svg class="back-footer" viewBox="0 0 600 42" aria-hidden="true">
      <polygon points="0,12 406,12 401,18 0,18" fill="var(--blush)"/>
      <polygon points="0,22 398,22 414,4 600,4 600,42 0,42" fill="var(--band)"/>
    </svg>
    <div class="back-web">www.velvetlantern-cakes.com</div>
  </section>
</body>
</html>
```